Superfoods Nutrition for Elderly

We need a thematic packaging design that fits our elderly nutrition products, that is based on our "3 Ws ethos" - eating Wisely, Widely & Wholly.

Wisely - selected superfoods and ingredients - NZ and other sources
Widely - based on the "rainbow diet" philosophy
Wholly - all natural, (no artificial flavours, colors etc). Formulated as complete meals (NOT supplementation)

Mediums:
- 400-450gram re-sealable doy packs
- 400-450gram re-sealable tin cans

Look n Feel:
Tuarango - https://tuarangokindness.com
Poli Vane - https://www.polvane.co.nz/
Juniper bluff - https://dinegladstaygood.co.nz/collections/cereals

The name of our products may/may not be “vital rori”. Our on-going research tells us that for the Asian market, an icon or character to personify our product may be a sound strategy. This is only for the designer to take note off.

Deliverables:
* 5 packaging designs in the range.
1x yellow + orange colored foods (star ingredient: “bright so” – passion fruit powder)
1x red colored foods (star ingredient: (star ingredient: - Manuka honey )
1x blues/purple colored foods: (star ingredient: lumoka blackcurrant)
1 x green coloured foods (star ingredient: Green kiwi)
1 x brown/white (star ingredients: harrowby’s grass fed bone broth)

brand name, please use “VitalRori” for now.

These will be the products:

Blue/purple: “Instant oatmeal porridge”
Ingredients: Rolled Baby Oats, Blueberries, Blackcurrant Powder, chia seeds, Blue Spirulina, Sheep’s Milk.
Star ingredient: Blackcurrant powder (support eyesight)

Brown/White: “Instant Brown Rice”
Ingredients: Organic Brown Rice, Grass fed bone broth powder, collagen peptide powder, black sesame seeds, onions and garlic powder, dried mushrooms, probiotics.
Star ingredient: Grass fed bone broth (support joint health)

Green: “Instant Smoothie”
Ingredients: Organic Green Kiwifruit, Kale powder, green apple powder, whey protein concentrate, probiotics, and sheep’s milk powder
Star ingredient: Organic green kiwi fruit(supports immunity)

Yellow/Orange “Instant Oatmeal”
Ingredients: Organic rolled baby oats, banana, organic passionfruit, apricot, dried mango, probiotics, cinnamon, sheep’s milk powder.
Star ingredient: Organic passionfruit(regulates blood glucose)

Red: “ instant amaranth cereal”
Ingredients: Organic amaranth, red apples, pomegranate, cranberries, Manuka honey powder, probiotics, sheep’s milk
Star ingredient: Manuka honey powder (anti-inflammatory)

Target Market(s)

Whose attention we are trying to grab?

Primary:
- 20 to 40 year olds buying these products for their parents/grand parents
- Health Nutrition conscious “golden agers”
Secondary
- Professional Caregivers to the elderly (homes, private hospitals etc)
- 40 year olds in the “prevention” mind set.

Font styles to use
Serif
Sans Serif

Colors

Designer to choose colors to be used in the design.

Requirements
Must have
• Mandatory:
• - clear visual que of the food color/s
• - "New Zealand" origin must come through strongly.
• - must have a blurp or feature of the star ingredient for each with mention of brand.
• e.g. for the blues+ purple, NZ blackcurrant powder for improved eyesight (cataract prevention).
• - icons for “heart health, “eyesight”, “mobility”, “gut-health”.
• - every other ingredient must be stated.
• The name of product may/may not be “vitalrori”. Our on-going research tells us that for the Asian market, an icon or character to personify our product may be a sound strategy. This is only for the designer to take note off.
Nice to have
• Desirables:
• Ingredient origin story - e.g blackcurrant comes from Timaru etc.
• (refer to Pemberlys destination marketing…)

```html
<!DOCTYPE html>
<html lang="en">
<head>
<meta charset="utf-8">
<title>VitalRori Instant Oatmeal – Label</title>
<link href="https://fonts.googleapis.com/css2?family=Cabin:wght@400;500;600;700&display=swap" rel="stylesheet">
<style>
  :root {
    --backdrop: #ececec;
    --label: #f7f7f7;
    --ink: #363636;
    --accent: #e2632b;
    --icon: #9c9c9c;
    --icon-text: #8a8a8a;
    --fruit: #9a4a66;
    --oat: #e6ddd1;
  }
  * { margin: 0; padding: 0; box-sizing: border-box; }
  html, body { width: 1200px; height: 1200px; overflow: hidden; }
  body {
    background: var(--backdrop);
    font-family: "Cabin", sans-serif;
    position: relative;
  }
  .label {
    position: absolute; left: 327px; top: 125px;
    width: 545px; height: 950px;
    background: var(--label);
  }
  .label > * { position: absolute; left: 50%; transform: translate(-50%, -50%); white-space: nowrap; text-align: center; }
  .brand { top: 138px; font-weight: 700; font-size: 68px; color: var(--ink); letter-spacing: -1px; line-height: 1; }
  .rule { height: 2px; background: var(--accent); opacity: .8; }
  .rule--title-top { top: 221px; width: 340px; }
  .product-name { top: 270px; font-weight: 500; font-size: 60px; color: var(--accent); line-height: 1; }
  .rule--title-bottom { top: 317px; width: 340px; }
  .made-with { top: 346px; font-size: 19px; color: var(--accent); font-weight: 500; }
  .star-ingredient { top: 378px; font-size: 30px; color: var(--accent); font-weight: 500; }
  .benefit-pill {
    top: 414px; background: var(--accent); color: #fff;
    font-size: 18px; font-weight: 500; padding: 1px 12px 2px; border-radius: 12px;
  }
  .hero-image {
    top: 617px; width: 430px; height: 285px; border-radius: 20px;
    background: linear-gradient(135deg, var(--fruit) 0%, #c79aa6 30%, var(--oat) 55%, var(--oat) 80%, #b8788a 100%);
  }
  .rule--icons-top { top: 778px; width: 350px; }
  .icon-row { top: 822px; display: flex; gap: 20px; }
  .icon-item { display: flex; flex-direction: column; align-items: center; width: 76px; }
  .icon-item svg { width: 48px; height: 48px; }
  .icon-item span { margin-top: 4px; font-size: 13px; color: var(--icon-text); }
  .rule--icons-bottom { top: 868px; width: 350px; }
  .net-weight { top: 903px; font-size: 20px; color: var(--accent); }
</style>
</head>
<body>
  <main class="label">
    <div class="brand">VitalRori</div>
    <div class="rule rule--title-top"></div>
    <h1 class="product-name">Instant Oatmeal</h1>
    <div class="rule rule--title-bottom"></div>
    <p class="made-with">Made With</p>
    <p class="star-ingredient">Organic Passion Fruit</p>
    <p class="benefit-pill">Regulates Blood Glucose</p>
    <div class="hero-image" role="img" aria-label="Photo of a bowl of oatmeal with milk beside halved purple passion fruits"></div>
    <div class="rule rule--icons-top"></div>
    <div class="icon-row">
      <div class="icon-item">
        <svg viewBox="0 0 64 64"><path fill="var(--icon)" d="M32 56 C10 40 4 30 4 20 C4 10 12 4 20 4 C26 4 30 8 32 12 C34 8 38 4 44 4 C52 4 60 10 60 20 C60 30 54 40 32 56Z"/></svg>
        <span>Heart Health</span>
      </div>
      <div class="icon-item">
        <svg viewBox="0 0 64 64"><path fill="var(--icon)" d="M2 32 C14 14 50 14 62 32 C50 50 14 50 2 32Z"/><circle cx="32" cy="32" r="13" fill="var(--label)"/><circle cx="32" cy="32" r="8" fill="var(--icon)"/></svg>
        <span>Eyesight</span>
      </div>
      <div class="icon-item">
        <svg viewBox="0 0 64 64" fill="none" stroke="var(--icon)" stroke-width="5" stroke-linecap="round" stroke-linejoin="round"><circle cx="40" cy="10" r="5" fill="var(--icon)" stroke="none"/><path d="M36 20 L28 36 L38 44 L34 58"/><path d="M28 36 L16 52"/><path d="M34 22 L20 26 L14 34"/><path d="M36 22 L44 32 L54 30"/></svg>
        <span>Mobility</span>
      </div>
      <div class="icon-item">
        <svg viewBox="0 0 64 64" fill="none" stroke="var(--icon)" stroke-width="3" stroke-linecap="round"><path d="M26 4 V16 C40 14 50 24 46 38 C42 50 28 50 22 46 C16 42 10 46 10 56"/><path d="M20 18 C12 22 12 32 20 34 C26 36 28 40 24 44"/><circle cx="42" cy="44" r="6"/><path d="M42 41 V47 M39 44 H45"/></svg>
        <span>Gut-Health</span>
      </div>
    </div>
    <div class="rule rule--icons-bottom"></div>
    <p class="net-weight">Net weight: 450g</p>
  </main>
</body>
</html>
```